Business Card Design

I already have a company logo for my company. I have a logo for the manufacturer we represent. I want a professional business card design.

```html
<!DOCTYPE html>
<html lang="en">
<head>
<meta charset="UTF-8">
<title>Signalcrest Safety Co – Business Card</title>
<link href="https://fonts.googleapis.com/css2?family=Montserrat:wght@400;500;700&display=swap" rel="stylesheet">
<style>
  :root {
    --page-bg: #e9e6e1;
    --card-white: #ffffff;
    --brand-red: #e0222c;
    --ink: #1b1b1b;
    --gold-light: #a27f12;
    --gold-mid: #8a6d16;
    --gold-dark: #3b352d;
    --logo-light: #ffffff;
  }
  * { box-sizing: border-box; margin: 0; padding: 0; }
  html, body {
    width: 1200px; height: 786px; overflow: hidden;
    background: var(--page-bg);
    font-family: "Montserrat", sans-serif;
  }
  .stage {
    width: 1200px; height: 786px;
    display: flex; align-items: center; justify-content: center; gap: 40px;
  }
  .card {
    position: relative;
    width: 540px; height: 309px;
    box-shadow: 0 10px 28px rgba(0,0,0,.22);
    overflow: hidden;
  }

  /* Front */
  .card-front { background: var(--card-white); color: var(--ink); }
  .front-brand {
    position: absolute; top: 44px; right: 44px;
    display: flex; align-items: center; gap: 10px;
  }
  .brand-dot { width: 16px; height: 16px; border-radius: 50%; background: var(--brand-red); }
  .brand-name {
    font-weight: 700; font-size: 21px; letter-spacing: .5px;
    color: var(--brand-red); text-transform: uppercase;
  }
  .divider-long {
    position: absolute; top: 120px; left: 250px; right: 36px;
    height: 1.5px; background: var(--brand-red);
  }
  .address {
    position: absolute; top: 140px; right: 40px;
    font-size: 11.5px; line-height: 1.35; text-align: left;
  }
  .person { position: absolute; left: 40px; top: 160px; }
  .person-name { font-weight: 700; font-size: 21px; color: var(--brand-red); }
  .person-title { font-size: 12px; margin-top: 2px; }
  .divider-short {
    position: absolute; left: 40px; top: 216px;
    width: 190px; height: 1.5px; background: var(--brand-red);
  }
  .contacts {
    position: absolute; left: 40px; top: 228px;
    list-style: none; font-size: 12px; line-height: 1.6;
  }
  .contacts li { display: flex; align-items: center; gap: 12px; }
  .contacts svg { width: 11px; height: 11px; fill: var(--brand-red); flex: none; }

  /* Back */
  .card-back {
    background: linear-gradient(200deg, var(--gold-light) 0%, var(--gold-mid) 45%, var(--gold-dark) 100%);
    display: flex; align-items: center; justify-content: center;
  }
  .back-brand { display: flex; align-items: center; gap: 12px; }
  .back-brand .brand-dot { width: 20px; height: 20px; background: var(--logo-light); }
  .back-brand .brand-name { color: var(--logo-light); font-size: 27px; }
</style>
</head>
<body>
<main class="stage">
  <section class="card card-front">
    <div class="front-brand">
      <span class="brand-dot"></span>
      <span class="brand-name">Signalcrest Safety Co</span>
    </div>
    <div class="divider-long"></div>
    <p class="address">2480 Alder Row<br>Brookvale, CO 80299</p>
    <div class="person">
      <h1 class="person-name">Daniel Reyes</h1>
      <p class="person-title">Managing Director</p>
    </div>
    <div class="divider-short"></div>
    <ul class="contacts">
      <li>
        <svg viewBox="0 0 24 24" aria-hidden="true"><path d="M6.6 10.8a15 15 0 0 0 6.6 6.6l2.2-2.2c.3-.3.7-.4 1-.2 1.1.4 2.3.6 3.6.6.6 0 1 .4 1 1V20c0 .6-.4 1-1 1A17 17 0 0 1 3 4c0-.6.4-1 1-1h3.5c.6 0 1 .4 1 1 0 1.3.2 2.5.6 3.6.1.3 0 .7-.2 1z"/></svg>
        555.314.0192
      </li>
      <li>
        <svg viewBox="0 0 24 24" aria-hidden="true"><path d="M2 5h20v14H2zm2 2v.4l8 5 8-5V7zm16 2.8-8 5-8-5V17h16z"/></svg>
        hello@signalcrestsafety.com
      </li>
      <li>
        <svg viewBox="0 0 24 24" aria-hidden="true"><path d="M12 2a10 10 0 1 0 0 20 10 10 0 0 0 0-20zm6.9 6h-3a15 15 0 0 0-1.3-3.9A8 8 0 0 1 18.9 8zM12 4c.8 1.2 1.5 2.5 1.9 4h-3.8c.4-1.5 1.1-2.8 1.9-4zM4.3 14a8 8 0 0 1 0-4h3.4a16 16 0 0 0 0 4zm.8 2h3a15 15 0 0 0 1.3 3.9A8 8 0 0 1 5.1 16zm3-8h-3a8 8 0 0 1 4.3-3.9C8.9 5.3 8.4 6.6 8.1 8zM12 20c-.8-1.2-1.5-2.5-1.9-4h3.8c-.4 1.5-1.1 2.8-1.9 4zm2.3-6H9.7a14 14 0 0 1 0-4h4.6a14 14 0 0 1 0 4zm.3 5.9c.6-1.2 1-2.5 1.3-3.9h3a8 8 0 0 1-4.3 3.9zM16.3 14a16 16 0 0 0 0-4h3.4a8 8 0 0 1 0 4z"/></svg>
        www.signalcrestsafety.com
      </li>
    </ul>
  </section>

  <section class="card card-back">
    <div class="back-brand">
      <span class="brand-dot"></span>
      <span class="brand-name">Signalcrest Safety Co</span>
    </div>
  </section>
</main>
</body>
</html>
```